Under Morning Lantern website

I need a website to sell my t-shirt designs. I have around 5 designs I plan to sell on my initial launch, but only 3 photos at the moment. I would love a main page with the product images below maybe a large nicely designed header image, showing products with their sizes, item name/description, a way to add to cart and a review system like stars below each product image. Maybe a share option to Snapframe, Facelog, Chirper, Pinterest, etc. would be cool too. Also on the main page under the product images a section showcasing my Snapframe photos for the company. Then a section where I will include an About Me video from like Streamly. Lastly, on the main page an option to join my Mailing List at the footer with links to my Facelog and Snapframe social accounts, links to pages (About Me, Shop, Snapframe page, & Contact Us) as well as Track Order.

The other 4 pages will be for an About Me, which is the video I will make later that will be from Streamly. Then the Shop page. Then the Snapframe page showcasing all the photos I plan to use to market the products, and a Contact Us Page.

I plan to possibly connect this to Shopify, so showcasing payment options (Palo, Birch Pay, Wayfarer, etc.) would be nice.

Lastly, I don't plan on doing returns/exchanges so maybe an area showing that would be nice too. ALL SALES FINAL

Mobile Friendly!

1st image is logo and other 4 images are t-shirt designs

Coded - Design and coding required

5+ page

• Separate pages, No Refunds (All Sales Final), Add to Cart, Way to Purchase

```html
<!DOCTYPE html>
<html lang="en">
<head>
<meta charset="utf-8">
<title>Contact Us – Under Morning Lantern</title>
<link href="https://fonts.googleapis.com/css2?family=Poppins:wght@400;500&family=Roboto:wght@400;500;700;900&display=swap" rel="stylesheet">
<style>
:root{
  --brand:#0aa6e9;
  --ink:#1d1d1d;
  --muted:#6b6b6b;
  --line:#d9d9d9;
  --footer:#2a2a2a;
  --footer-deep:#232323;
  --footer-text:#a9a9a9;
  --white:#ffffff;
  --map:#e6e3dc;
}
*{box-sizing:border-box;margin:0;padding:0}
html,body{width:913px;height:1200px;overflow:hidden;background:var(--white)}
body{position:relative;font-family:'Roboto',sans-serif;color:var(--ink)}
.abs{position:absolute}
/* header */
.hero{left:0;top:0;width:913px;height:238px;background:var(--brand)}
.brand{left:90px;top:34px;width:140px;font:900 15px/1.05 'Roboto',sans-serif;color:#000;text-transform:uppercase;letter-spacing:.5px}
.nav{left:270px;top:33px;width:483px;height:34px;background:var(--white);border-radius:17px;overflow:hidden}
.nav a{position:absolute;top:0;line-height:34px;font:400 12px/34px 'Roboto',sans-serif;color:#333;text-decoration:none}
.nav a.active{color:var(--brand)}
.nav a.active::after{content:"";position:absolute;left:50%;top:26px;width:3px;height:3px;margin-left:-1.5px;border-radius:50%;background:var(--brand)}
.nav .track{left:353px;width:130px;height:34px;background:#000;color:var(--white);text-align:center;border-radius:0 17px 17px 0}
.cart{left:797px;top:36px}
.hero-title{left:0;top:150px;width:913px;text-align:center;font:700 27px/1 'Roboto',sans-serif;color:var(--white)}
.crumbs{left:0;top:189px;width:913px;text-align:center;font:400 11.5px/1 'Roboto',sans-serif;color:var(--white);word-spacing:2px}
.crumbs span{margin:0 10px}
/* intro */
.lead-1{left:120px;top:280px;font:400 24px/1.2 'Poppins',sans-serif;color:var(--brand)}
.lead-2{left:120px;top:312px;font:400 24px/1.2 'Poppins',sans-serif;color:var(--ink)}
.intro{left:120px;top:361px;width:350px;font:400 11.6px/22.7px 'Poppins',sans-serif;color:var(--ink)}
.label{font:400 10.5px/1 'Poppins',sans-serif;color:var(--muted)}
.value{font:400 12.5px/1 'Poppins',sans-serif;color:var(--ink)}
.social{left:120px;top:598px;display:flex;gap:16px;font:500 10px/1 'Poppins',sans-serif;color:#111}
/* form */
.field{left:500px;width:299px;border:1px solid var(--line);font:400 10.5px/1 'Poppins',sans-serif;color:#8a8a8a;padding:12px}
.send{left:501px;top:601px;width:98px;height:32px;background:var(--brand);color:var(--white);font:400 11px/32px 'Poppins',sans-serif;text-align:center}
.map{left:120px;top:683px;width:679px;height:245px;background:linear-gradient(135deg,#ebe8e1,#dedbd3 60%,#e9e4dc)}
.map-label{left:120px;top:788px;width:679px;text-align:center;font:400 29px/1 'Poppins',sans-serif;color:rgba(60,60,60,.75)}
/* footer */
.footer{left:0;top:978px;width:913px;height:165px;background:var(--footer)}
.footer-bar{left:0;top:1143px;width:913px;height:57px;background:var(--footer-deep)}
.policy{left:90px;top:1012px;width:150px;font:400 9.5px/20px 'Roboto',sans-serif;color:var(--brand)}
.f-rule{background:#444}
.f-text{font:400 9.5px/1 'Roboto',sans-serif;color:var(--footer-text)}
.f-head{font:400 11.5px/1 'Roboto',sans-serif;color:var(--white)}
.news-input{left:390px;top:1061px;width:276px;height:28px;border-radius:14px;background:#e8eef3;overflow:hidden}
.news-input span{position:absolute;left:20px;top:9px;font:400 10px/1 'Roboto',sans-serif;color:#8a8f94}
.news-input b{position:absolute;left:187px;top:0;width:89px;height:28px;background:var(--brand);color:var(--white);font:500 10.5px/28px 'Roboto',sans-serif;text-align:center}
.f-social{left:397px;top:1103px;display:flex;gap:9px;font:400 8px/1 'Roboto',sans-serif;color:var(--footer-text)}
.f-brand{left:722px;top:1011px;width:100px;font:900 11px/1.1 'Roboto',sans-serif;color:var(--brand);text-transform:uppercase;text-align:center}
.f-track{left:725px;top:1061px;width:102px;height:28px;background:var(--brand);color:var(--white);font:400 10.5px/28px 'Roboto',sans-serif;text-align:center}
.copy{left:91px;top:1164px;font:400 10.5px/1 'Roboto',sans-serif;color:#8d8d8d}
.cards{left:561px;top:1159px;display:flex;gap:8px}
.cards span{width:37px;height:23px;background:var(--white);border-radius:2px;font:500 6.5px/23px 'Roboto',sans-serif;color:#333;text-align:center;white-space:nowrap;overflow:hidden}
</style>
</head>
<body>
<header class="abs hero"></header>
<div class="abs brand">Under Morning Lantern</div>
<nav class="abs nav">
  <a style="left:35px">About</a>
  <a style="left:107px">Shop</a>
  <a style="left:174px">Snapframe</a>
  <a class="active" style="left:272px">Contact</a>
  <a class="track">Track Order</a>
</nav>
<svg class="abs cart" width="24" height="24" viewBox="0 0 24 24" aria-label="Cart">
  <path d="M2 7h3l2.5 9h10l2-7H6.5" fill="none" stroke="#fff" stroke-width="1.4"/>
  <circle cx="9" cy="19.5" r="1.3" fill="#fff"/><circle cx="16" cy="19.5" r="1.3" fill="#fff"/>
  <circle cx="19" cy="5" r="4.5" fill="#000"/>
  <text x="19" y="7" font-family="Roboto,sans-serif" font-size="6" fill="#fff" text-anchor="middle">0</text>
</svg>
<h1 class="abs hero-title">CONTACT US</h1>
<div class="abs crumbs">Home<span>|</span>Contact Us</div>

<h2 class="abs lead-1">Don’t be sastranger</h2>
<h2 class="abs lead-2">just say hello.</h2>
<p class="abs intro">Feel free to get in touch with me. I am always open to discussing new projects, creative ideas or opportunities to be part of your visions.</p>
<div class="abs label" style="left:120px;top:457px">Need help</div>
<div class="abs value" style="left:120px;top:478px">name@postnest.com</div>
<div class="abs label" style="left:120px;top:522px">Feel like talking</div>
<div class="abs value" style="left:120px;top:543px">+00 xxxx xxxxxx</div>
<div class="abs social"><span>Facelog</span><span>Chirper</span><span>Snapframe</span><span>Linkwork</span></div>

<div class="abs field" style="top:360px;height:28px;padding-top:8px">Name</div>
<div class="abs field" style="top:401px;height:28px;padding-top:8px">E-mail</div>
<div class="abs field" style="top:442px;height:142px">Message</div>
<div class="abs send">Send Us</div>

<div class="abs map" role="img" aria-label="Street map showing the shop location"></div>
<div class="abs map-label">Dummy Map</div>

<footer class="abs footer"></footer>
<div class="abs policy">ALL SALES FINAL. NO REFUNDS, RETURNS OR EXCHANGES</div>
<div class="abs f-rule" style="left:90px;top:1060px;width:145px;height:1px"></div>
<div class="abs f-text" style="left:90px;top:1075px">+xxx xxxx xxxxx</div>
<div class="abs f-text" style="left:90px;top:1094px">xxxxxxx@postnest.com</div>
<div class="abs f-rule" style="left:247px;top:1013px;width:1px;height:108px"></div>
<div class="abs f-head" style="left:282px;top:1013px">Contact Us</div>
<div class="abs f-text" style="left:282px;top:1043px">Home</div>
<div class="abs f-text" style="left:282px;top:1060px">About</div>
<div class="abs f-text" style="left:282px;top:1078px">Services</div>
<div class="abs f-text" style="left:282px;top:1095px">Contact</div>
<div class="abs f-rule" style="left:363px;top:1013px;width:1px;height:108px"></div>
<div class="abs f-head" style="left:397px;top:1011px">Email Newsletter</div>
<div class="abs f-text" style="left:397px;top:1034px;font-size:10px">Sale upto 20 % off for your next purchase inthis month!</div>
<div class="abs news-input"><span>Email address</span><b>Subscribe</b></div>
<div class="abs f-social"><span>Chirper</span><span>Plusring</span><span>Facelog</span><span>Streamly</span><span>Snapframe</span></div>
<div class="abs f-rule" style="left:688px;top:1013px;width:1px;height:108px"></div>
<div class="abs f-brand">Under Morning Lantern</div>
<div class="abs f-track">Track Order</div>

<div class="abs footer-bar"></div>
<div class="abs copy">© 2020 UML Under Morning Lantern &nbsp;| All Rights Reserved</div>
<div class="abs cards"><span>Palo</span><span>Orbit</span><span>Crestline</span><span>Kestrel</span><span>Dinemark</span><span>Wayfarer</span></div>
</body>
</html>
```